Velborix advertisement one page flyer design

We need a flyer design for our company to advertise what we offer, it only needs to be one sided, approx A5 in size.
Our logo: http://velborix-example.com/images/logo.png (I will provide in high-res later)
We offer, website design, development, bespoke applications. We would like to advertise that we can be hired for short term contracts for companies who need help with their work load.
Some of, but not limited to the systems we build are content management systems, e-commerce systems & event booking systems.
Our strap line is "We design, develop and deliver", a nice sleek redesign of the image on our website would be nice, but not required 100% - http://velborix-example.com/
Other details to put on the flyer:-
Email: hello@velborix-example.com
Tel: 01632 960 417
Address: Velborix Ltd, Crest Suites, Dunmoor Road, Cheltenham, GL53 4QT
We welcome any other ideas.

```html
<!DOCTYPE html>
<html lang="en">
<head>
<meta charset="utf-8">
<title>Velborix flyer</title>
<link rel="stylesheet" href="https://fonts.googleapis.com/css2?family=Open+Sans:wght@700;800&family=Patrick+Hand&family=Russo+One&family=Arimo:wght@400;700&display=swap">
<style>
  :root {
    --page: #e9e6e2;
    --orange: #e87511;
    --orange-deep: #9c3405;
    --orange-bright: #f7a23a;
    --grey-panel: #999999;
    --ink: #222222;
    --ink-soft: #474747;
    --logo-grey: #595959;
    --white: #ffffff;
  }
  * { box-sizing: border-box; margin: 0; padding: 0; }
  html, body { width: 891px; height: 1200px; overflow: hidden; background: var(--page); }
  .flyer {
    position: absolute; left: 57px; top: 47px; width: 778px; height: 1105px;
    background: var(--grey-panel); overflow: hidden;
  }
  .hero {
    position: absolute; left: 0; top: 0; width: 778px; height: 338px;
    background: linear-gradient(90deg, var(--orange-deep) 0%, #c7500c 45%, var(--orange) 100%);
    border-bottom: 2px solid var(--white);
  }
  .hero-art {
    position: absolute; right: 0; top: 0; width: 380px; height: 336px;
    background: radial-gradient(circle at 60% 35%, #ffd48a 0%, var(--orange-bright) 30%, var(--orange) 65%, rgba(232,117,17,0) 100%);
  }
  .brand {
    position: absolute; left: 22px; top: 26px;
    font-family: "Open Sans", sans-serif; font-weight: 800; font-size: 70px;
    letter-spacing: -1px; color: var(--logo-grey); line-height: 1;
  }
  .hero-copy {
    position: absolute; left: 18px; top: 156px; width: 440px;
    font-family: "Open Sans", sans-serif; font-weight: 700; font-size: 19px;
    line-height: 28px; color: var(--white);
  }
  .hero-copy p + p { margin-top: 28px; }
  .section-title {
    position: absolute; left: 0; width: 778px; text-align: center;
    font-family: "Patrick Hand", cursive; font-size: 44px; color: var(--ink); line-height: 1;
  }
  .how-title { top: 366px; }
  .solutions-title { top: 680px; }
  .rule { position: absolute; top: 702px; height: 3px; background: var(--orange); }
  .rule-left { left: 0; width: 130px; }
  .rule-right { right: 0; width: 128px; }
  .step { position: absolute; top: 460px; width: 200px; text-align: center; }
  .step svg { display: block; margin: 0 auto; }
  .step-name {
    margin-top: 6px; font-family: "Russo One", sans-serif; font-size: 58px;
    color: var(--ink-soft); line-height: 1;
  }
  .solution { position: absolute; width: 240px; text-align: center; }
  .solution svg { display: block; margin: 0 auto; }
  .solution-name {
    margin-top: 2px; font-family: "Arimo", sans-serif; font-weight: 700;
    font-size: 17px; color: var(--ink);
  }
  .contact {
    position: absolute; left: 0; top: 1021px; width: 778px; height: 84px;
    background: var(--white); text-align: center; color: var(--ink);
    font-family: "Arimo", sans-serif;
  }
  .contact-line { font-size: 24px; margin-top: 10px; display: flex; justify-content: center; align-items: center; gap: 8px; }
  .contact-address { font-size: 19px; margin-top: 6px; display: flex; justify-content: center; align-items: center; gap: 8px; }
  .gap { width: 14px; }
</style>
</head>
<body>
<main class="flyer">
  <header class="hero">
    <div class="hero-art" role="img" aria-label="Photo of a hand touching glowing orange web icons"></div>
    <div class="brand">Velborix</div>
    <div class="hero-copy">
      <p>We offer, website design, development, bespoke application</p>
      <p>We can be hired for short term contract for. companies who need help with then work load</p>
    </div>
  </header>

  <h2 class="section-title how-title">How It Works?</h2>

  <div class="step" style="left:43px">
    <svg width="100" height="100" viewBox="0 0 100 100" aria-hidden="true">
      <circle cx="50" cy="50" r="48" fill="var(--orange)"/>
      <path d="M32 30 L70 70 M70 30 L32 70" stroke="#fff" stroke-width="9" stroke-linecap="round"/>
    </svg>
    <div class="step-name">design</div>
  </div>
  <div class="step" style="left:281px">
    <svg width="100" height="100" viewBox="0 0 100 100" aria-hidden="true">
      <circle cx="50" cy="50" r="48" fill="var(--orange)"/>
      <path d="M30 30 L70 70" stroke="#fff" stroke-width="8" stroke-linecap="round"/>
      <path d="M70 30 L30 70" stroke="#fff" stroke-width="8" stroke-linecap="round"/>
      <circle cx="72" cy="28" r="9" fill="#fff"/>
    </svg>
    <div class="step-name">devlop</div>
  </div>
  <div class="step" style="left:520px">
    <svg width="100" height="100" viewBox="0 0 100 100" aria-hidden="true">
      <circle cx="50" cy="50" r="48" fill="var(--orange)"/>
      <path d="M34 24 L40 24 L40 72 L70 72" stroke="#fff" stroke-width="5" fill="none" stroke-linecap="round"/>
      <rect x="46" y="48" width="20" height="20" fill="#fff"/>
      <rect x="50" y="32" width="14" height="14" fill="#fff"/>
      <circle cx="42" cy="78" r="5" fill="#fff"/>
    </svg>
    <div class="step-name">deliver</div>
  </div>

  <div class="rule rule-left"></div>
  <h2 class="section-title solutions-title">Solutions We Provide</h2>
  <div class="rule rule-right"></div>

  <div class="solution" style="left:0; top:780px">
    <svg width="62" height="62" viewBox="0 0 62 62" aria-hidden="true"><circle cx="31" cy="31" r="31" fill="var(--orange)"/><rect x="19" y="14" width="22" height="30" rx="2" fill="#fff"/><path d="M23 22h14M23 28h14M23 34h10" stroke="var(--orange)" stroke-width="2"/></svg>
    <div class="solution-name">Content Management</div>
  </div>
  <div class="solution" style="left:266px; top:780px">
    <svg width="62" height="62" viewBox="0 0 62 62" aria-hidden="true"><circle cx="31" cy="31" r="31" fill="var(--orange)"/><circle cx="28" cy="31" r="13" fill="none" stroke="#fff" stroke-width="2.5"/><path d="M15 31h26M28 18v26" stroke="#fff" stroke-width="2"/><path d="M40 40 L50 24" stroke="#fff" stroke-width="4" stroke-linecap="round"/></svg>
    <div class="solution-name">Web Design</div>
  </div>
  <div class="solution" style="left:553px; top:780px">
    <svg width="62" height="62" viewBox="0 0 62 62" aria-hidden="true"><circle cx="31" cy="31" r="31" fill="var(--orange)"/><circle cx="31" cy="31" r="16" fill="none" stroke="#fff" stroke-width="2.5"/><path d="M24 31a7 7 0 1 0 7-7" fill="none" stroke="#fff" stroke-width="2.5"/></svg>
    <div class="solution-name">Bespoke System</div>
  </div>
  <div class="solution" style="left:0; top:905px">
    <svg width="62" height="62" viewBox="0 0 62 62" aria-hidden="true"><circle cx="31" cy="31" r="31" fill="var(--orange)"/><circle cx="30" cy="30" r="15" fill="none" stroke="#fff" stroke-width="2.5"/><path d="M15 30h30M30 15v30" stroke="#fff" stroke-width="2"/><rect x="38" y="38" width="10" height="8" fill="#fff"/></svg>
    <div class="solution-name">e-commerce</div>
  </div>
  <div class="solution" style="left:266px; top:905px">
    <svg width="62" height="62" viewBox="0 0 62 62" aria-hidden="true"><circle cx="31" cy="31" r="31" fill="var(--orange)"/><rect x="18" y="20" width="22" height="24" rx="2" fill="none" stroke="#fff" stroke-width="2.5"/><path d="M28 34 L46 14" stroke="#fff" stroke-width="4" stroke-linecap="round"/></svg>
    <div class="solution-name">Subscription System</div>
  </div>
  <div class="solution" style="left:553px; top:905px">
    <svg width="62" height="62" viewBox="0 0 62 62" aria-hidden="true"><circle cx="31" cy="31" r="31" fill="var(--orange)"/><rect x="18" y="26" width="26" height="6" fill="#fff"/><rect x="18" y="34" width="26" height="6" fill="#fff"/><rect x="18" y="42" width="26" height="6" fill="#fff"/><path d="M20 14 L26 20 M42 14 L36 20" stroke="#fff" stroke-width="2.5"/></svg>
    <div class="solution-name">Domain &amp; Hosting</div>
  </div>

  <footer class="contact">
    <div class="contact-line">
      <svg width="16" height="22" viewBox="0 0 16 22" aria-hidden="true"><path d="M5 2 L2 4 C0 10 4 18 11 21 L14 18 L10 14 L8 15 C6 13 5 10 5 8 L7 7 Z" fill="none" stroke="var(--ink)" stroke-width="1.8"/></svg>
      <span>01632 960 417</span><span class="gap"></span>
      <svg width="22" height="16" viewBox="0 0 22 16" aria-hidden="true"><rect x="1" y="1" width="20" height="14" fill="none" stroke="var(--ink)" stroke-width="2"/><path d="M1 1 L11 9 L21 1" fill="none" stroke="var(--ink)" stroke-width="2"/></svg>
      <span>hello@velborix-example.com</span>
    </div>
    <div class="contact-address">
      <svg width="14" height="20" viewBox="0 0 14 20" aria-hidden="true"><path d="M7 0a7 7 0 0 0-7 7c0 5 7 13 7 13s7-8 7-13a7 7 0 0 0-7-7z" fill="var(--ink)"/><circle cx="7" cy="7" r="2.5" fill="#fff"/></svg>
      <span>Velborix Ltd, Crest Suites, Dunmoor Road, Cheltenham, GL53 4QT</span>
    </div>
  </footer>
</main>
</body>
</html>
```